Coffeeshop menu for filter tip

We want to have a cannabis (coffeeshop) menu in the size 25mm wide x 60mm wide. Some examples attached.

it must have the following text:
Menu

WEED p/g
Oblivane €16
Cloudplum €14
Tide Runner €14
Quincefig €16
Mega Marsh €14
Grey Heron €14

HASH p/g
Tashar Amber €12
Pebble Frost€11
Lime Dunes €14
Ash Petal €10

Target Market(s)

tourist in Amsterdam

Requirements
Nice to have
• cannabis sign leaf
• No Cigarettes allowed symbol

```html
<!DOCTYPE html>
<html lang="en">
<head>
<meta charset="utf-8">
<title>Coffeeshop Menu</title>
<link rel="stylesheet" href="https://fonts.googleapis.com/css2?family=Alfa+Slab+One&family=Oswald:wght@500&family=Montserrat:wght@600&display=swap">
<style>
  :root {
    --backdrop: #606060;
    --leaf-green: #7ab63f;
    --shade-green: #5f9a36;
    --band-white: #ffffff;
    --title-green: #7ab63f;
    --ink-white: #ffffff;
    --sign-red: #e0262b;
    --sign-black: #111111;
  }
  html, body {
    margin: 0;
    padding: 0;
    width: 686px;
    height: 1200px;
    overflow: hidden;
    background: var(--backdrop);
  }
  .menu-card {
    position: absolute;
    left: 136px;
    top: 100px;
    width: 417px;
    height: 1000px;
  }
  .menu-card svg { display: block; }
  .card-field { fill: var(--leaf-green); }
  .shade { fill: var(--shade-green); opacity: 0.85; }
  .title-band { fill: var(--band-white); }
  .menu-title {
    font-family: "Alfa Slab One", serif;
    font-size: 100px;
    fill: var(--title-green);
  }
  .section-heading {
    font-family: "Alfa Slab One", serif;
    font-size: 48px;
    fill: var(--ink-white);
  }
  .unit-label {
    font-family: "Montserrat", sans-serif;
    font-weight: 600;
    font-size: 21px;
    fill: var(--ink-white);
  }
  .section-rule { stroke: var(--ink-white); stroke-width: 1.5; }
  .item-name, .item-price {
    font-family: "Oswald", sans-serif;
    font-weight: 500;
    font-size: 32px;
    fill: var(--ink-white);
  }
  .item-price { text-anchor: end; }
  .notice-text {
    font-family: "Montserrat", sans-serif;
    font-weight: 600;
    font-size: 27px;
    fill: var(--ink-white);
  }
  .sign-ring { fill: none; stroke: var(--sign-red); stroke-width: 5; }
  .sign-bar { stroke: var(--sign-red); stroke-width: 5; }
  .sign-cigarette { fill: var(--sign-black); }
  .sign-smoke { fill: none; stroke: var(--sign-black); stroke-width: 2.5; stroke-linecap: round; }
</style>
</head>
<body>
<div class="menu-card">
  <svg width="417" height="1000" viewBox="0 0 417 1000">
    <rect class="card-field" x="0" y="0" width="417" height="1000" role="img" aria-label="Green background with faint repeating cannabis leaf pattern"/>

    <polygon class="shade" points="0,17 263,86 0,86"/>
    <rect class="title-band" x="0" y="86" width="417" height="158"/>
    <polygon class="shade" points="75,244 417,244 417,302"/>

    <text class="menu-title" x="208" y="212" text-anchor="middle" textLength="270" lengthAdjust="spacingAndGlyphs">MENU</text>

    <g class="menu-section weed">
      <text class="section-heading" x="48" y="339" textLength="119" lengthAdjust="spacingAndGlyphs">WEED</text>
      <text class="unit-label" x="357" y="337" text-anchor="end">P/G</text>
      <line class="section-rule" x1="48" y1="353" x2="370" y2="353"/>
      <text class="item-name" x="48" y="396">Oblivane</text><text class="item-price" x="352" y="396">€16</text>
      <text class="item-name" x="48" y="437">Cloudplum</text><text class="item-price" x="352" y="437">€14</text>
      <text class="item-name" x="48" y="478">Tide Runner</text><text class="item-price" x="352" y="478">€14</text>
      <text class="item-name" x="48" y="518">Quincefig</text><text class="item-price" x="352" y="518">€16</text>
      <text class="item-name" x="48" y="559">Mega Marsh</text><text class="item-price" x="352" y="559">€14</text>
      <text class="item-name" x="48" y="600">Grey Heron</text><text class="item-price" x="352" y="600">€14</text>
    </g>

    <g class="menu-section hash">
      <text class="section-heading" x="48" y="696" textLength="112" lengthAdjust="spacingAndGlyphs">HASH</text>
      <text class="unit-label" x="357" y="697" text-anchor="end">P/G</text>
      <line class="section-rule" x1="48" y1="714" x2="370" y2="714"/>
      <text class="item-name" x="48" y="756">Tashar Amber</text><text class="item-price" x="352" y="756">€12</text>
      <text class="item-name" x="48" y="797">Pebble Frost</text><text class="item-price" x="352" y="797">€11</text>
      <text class="item-name" x="48" y="838">Lime Dunes</text><text class="item-price" x="352" y="838">€14</text>
      <text class="item-name" x="48" y="879">Ash Petal</text><text class="item-price" x="352" y="879">€10</text>
    </g>

    <g class="no-smoking-notice">
      <g class="no-smoking-sign">
        <rect class="sign-cigarette" x="85" y="950" width="36" height="7"/>
        <path class="sign-smoke" d="M114 946 c-4 -5 4 -9 0 -16 M119 946 c-3 -5 4 -8 1 -14"/>
        <line class="sign-bar" x1="84" y1="930" x2="122" y2="968"/>
        <circle class="sign-ring" cx="103" cy="949" r="26"/>
      </g>
      <text class="notice-text" x="146" y="960">No Cigarettes</text>
    </g>
  </svg>
</div>
</body>
</html>
```